Spirits Bottle Label-Brand Name Reed & Barrow

Design a spirits bottle label per specifications outlined. Label size Front 3.875x 4.5,Back 2x4, topper 1x5.7. Must have established 2020, 40% Alcohol by volume. 40 proof. Sherry Cask Settled. Bottle # 1 of 1320. Caribbean Rum. Trademark logo must be on the label. Back of label has to have all the information outlined in photo. Topper & Front of the label the designer can you his creativity. Color scheme is negotiable and designers can be creative.

Target Market(s)

Adults aged 21 with an appealing appearance that caters to a young professionals and seasoned adults

Font styles to use
Sans Serif

Colors
886aae
33b8a4
33a6d7

Requirements
Must have
• -Reed & Barrow Trademark Logo which is attached.
-Caribbean Rum
-40% Alcohol By Volume
-80 Proof
-Sherry Cask Settled
-Established 2020

```html
<!DOCTYPE html>
<html lang="en">
<head>
<meta charset="utf-8">
<title>Reed &amp; Barrow Caribbean Rum Label</title>
<link href="https://fonts.googleapis.com/css2?family=Allura&family=Bebas+Neue&family=Lobster&family=Rye&family=Fira+Sans+Condensed:wght@700&display=swap" rel="stylesheet">
<style>
  :root {
    --paper: #e6ddcf;
    --ink: #0d0b09;
    --sepia-dark: #1b1611;
    --sepia-mid: #4a3f33;
    --sepia-light: #8a7b69;
    --gold: #c9a24f;
    --gold-light: #f4eab8;
    --gold-deep: #8f5f22;
    --silver: #d4d4d6;
    --white: #ffffff;
  }
  * { margin: 0; padding: 0; box-sizing: border-box; }
  html, body { width: 1200px; height: 1033px; overflow: hidden; background: var(--paper); }
  .label {
    position: relative;
    width: 1200px;
    height: 1033px;
    background: var(--paper);
    overflow: hidden;
  }
  .still-life {
    position: absolute;
    left: 58px; top: 52px;
    width: 1078px; height: 934px;
    background:
      radial-gradient(ellipse 260px 230px at 695px 330px, #b6a996 0%, #8c806f 40%, rgba(60,52,43,0) 100%),
      radial-gradient(ellipse 500px 300px at 560px 700px, #6e6253 0%, rgba(40,34,28,0) 100%),
      linear-gradient(160deg, var(--ink) 0%, var(--sepia-dark) 35%, var(--sepia-mid) 70%, var(--sepia-light) 100%);
    clip-path: polygon(0.6% 3%, 8% 1.2%, 22% 2.4%, 40% 0.6%, 58% 2%, 76% 0.8%, 92% 2.2%, 99.4% 1%, 98.6% 14%, 100% 30%, 98.8% 48%, 100% 66%, 98.4% 84%, 99.6% 98.6%, 84% 97.4%, 66% 99.2%, 48% 97.8%, 30% 99.4%, 12% 97.6%, 0.4% 99%, 1.4% 82%, 0% 62%, 1.2% 42%, 0% 22%);
  }
  .kicker {
    position: absolute;
    left: 150px; top: 104px;
    width: 360px;
    font-family: "Allura", cursive;
    font-size: 56px;
    color: var(--silver);
    text-align: center;
    line-height: 1;
    white-space: nowrap;
  }
  .category {
    position: absolute;
    left: 140px; top: 162px;
    width: 360px;
    font-family: "Bebas Neue", sans-serif;
    font-weight: 400;
    color: var(--gold);
    text-align: center;
    line-height: 0.88;
  }
  .category .line-1 { display: block; font-size: 90px; }
  .category .line-2 { display: block; font-size: 122px; }
  .flourish {
    position: absolute;
    top: 258px;
    width: 56px; height: 56px;
    background: rgba(201,162,79,0.35);
    border-radius: 6px;
  }
  .flourish.left { left: 164px; }
  .flourish.right { left: 422px; }
  .rule {
    position: absolute;
    left: 258px; top: 335px;
    width: 124px; height: 3px;
    background: var(--gold);
    border-radius: 2px;
  }
  .brand-art { position: absolute; left: 0; top: 0; width: 1200px; height: 1033px; }
  .script-text { font-family: "Lobster", cursive; }
  .brand-name { font-family: "Rye", serif; }
  .specs {
    position: absolute;
    left: 140px; top: 862px;
    display: flex;
    font-family: "Fira Sans Condensed", sans-serif;
    font-weight: 700;
    color: var(--gold);
  }
  .spec-volume { font-size: 30px; line-height: 1.05; text-align: right; padding-right: 12px; width: 76px; }
  .spec-divider { width: 2px; height: 66px; background: var(--silver); opacity: 0.7; margin-top: 2px; }
  .spec-pair { padding: 0 16px; text-align: center; font-size: 22px; white-space: nowrap; }
  .spec-pair .top { display: block; padding-bottom: 7px; border-bottom: 2px solid var(--silver); }
  .spec-pair .bottom { display: block; padding-top: 6px; }
</style>
</head>
<body>
<main class="label">
  <div class="still-life" role="img" aria-label="Sepia still-life photograph of a human skull resting on old leather books, with a flintlock pistol, draped cloth, a bottle, pearls and an old map on a wooden table"></div>

  <p class="kicker">Vintage Crafted</p>
  <h2 class="category"><span class="line-1">Caribbean</span><span class="line-2">Rum</span></h2>
  <div class="flourish left" role="img" aria-label="Small gold ornamental flourish"></div>
  <div class="flourish right" role="img" aria-label="Small gold ornamental flourish"></div>
  <div class="rule"></div>

  <svg class="brand-art" viewBox="0 0 1200 1033" aria-labelledby="brand-title">
    <title id="brand-title">Authentic Reed &amp; Barrow, Sherry Cask Settled</title>
    <defs>
      <linearGradient id="gold-fill" x1="0" y1="0" x2="1" y2="0">
        <stop offset="0" stop-color="#8f5f22"/>
        <stop offset="0.3" stop-color="#d3ae62"/>
        <stop offset="0.5" stop-color="#f4eab8"/>
        <stop offset="0.72" stop-color="#c99a48"/>
        <stop offset="1" stop-color="#8f5f22"/>
      </linearGradient>
    </defs>
    <g transform="rotate(-12 330 540)">
      <text class="script-text" x="190" y="572" font-size="70" fill="#0d0b09">Authentic</text>
      <text class="script-text" x="186" y="567" font-size="70" fill="#d4d4d6">Authentic</text>
    </g>
    <g transform="rotate(-11.6 600 690)">
      <text class="brand-name" x="604" y="760" font-size="118" text-anchor="middle" fill="#0d0b09">REED &amp; BARROW</text>
      <text class="brand-name" x="596" y="752" font-size="118" text-anchor="middle" fill="url(#gold-fill)" stroke="#ffffff" stroke-width="2.5" paint-order="stroke">REED &amp; BARROW</text>
    </g>
    <g transform="rotate(-13 890 760)">
      <text class="script-text" x="716" y="818" font-size="44" fill="#0d0b09">Sherry Cask Settled</text>
      <text class="script-text" x="713" y="814" font-size="44" fill="#d4d4d6">Sherry Cask Settled</text>
    </g>
  </svg>

  <div class="specs">
    <div class="spec-volume">750<br>ML.</div>
    <div class="spec-divider"></div>
    <div class="spec-pair"><span class="top">40% alc./vol.</span><span class="bottom">Bottle 1 - 1320</span></div>
    <div class="spec-divider"></div>
    <div class="spec-pair"><span class="top">80 Proof</span><span class="bottom">Est. 2020</span></div>
  </div>
</main>
</body>
</html>
```